New career and executive coaching business needs a business card design including logo

Company name: 'Bramblefield Growth Partners.' The aim of my coaching engagements is to help people improve their communication in the workplace and achieve their career goals. The process involves working with individuals to help them uncover their strengths and talents, then leverage those to improve their working lives. The Tarwick Inventory is the starting point to the process. I am after an exciting and interesting business card design (including logo)which is professional yet will still get people's attention.

Industry/Entity Type

Business

Contact Information for Business Card

Name: Malcolm Dervaney
Position: Owner
Address: 58 Quorrin Ct, Elmbridge Vic 3190
Phone: 0418923047
Website: bramblefieldgrowth.com.au
Email: malcolm@bgp.com.au

Colors
33a6d7
00a990
0355a3
3176b5

Requirements
Must have
• logo

```html
<!DOCTYPE html>
<html lang="en">
<head>
<meta charset="utf-8">
<title>Bramblefield Growth Partners – Business Card</title>
<link rel="stylesheet" href="https://fonts.googleapis.com/css2?family=Open+Sans:wght@400;600;700&display=swap">
<style>
  :root {
    --sky: #33a6d7;
    --royal: #0355a3;
    --mid-blue: #3176b5;
    --ink: #1b1b1b;
    --paper: #ffffff;
    --backdrop: #e9e6e3;
  }
  * { box-sizing: border-box; margin: 0; padding: 0; }
  html, body {
    width: 1200px; height: 900px; overflow: hidden;
    background: var(--backdrop);
    font-family: "Open Sans", sans-serif;
  }
  .stage { position: relative; width: 1200px; height: 900px; }

  .card {
    position: absolute;
    background: var(--paper);
    box-shadow: 0 6px 18px rgba(0,0,0,0.18);
    overflow: hidden;
  }

  /* Front */
  .card--front { left: 77px; top: 34px; width: 588px; height: 364px; }
  .brand {
    position: absolute; left: 32px; top: 56px;
    display: flex; align-items: center; gap: 14px;
  }
  .brand__mark { width: 30px; height: 30px; background: var(--royal); }
  .brand__name {
    font-size: 25px; font-weight: 600; color: var(--ink); letter-spacing: -0.2px;
  }
  .front__band {
    position: absolute; left: 0; top: 156px; width: 100%; height: 208px;
    background: linear-gradient(180deg, var(--sky) 0%, var(--mid-blue) 60%, var(--royal) 100%);
    color: var(--paper);
    padding: 22px 0 0 32px;
  }
  .person__name { font-size: 21px; font-weight: 700; line-height: 1.1; }
  .person__role { font-size: 14px; line-height: 1.3; margin-bottom: 18px; }
  .contact { list-style: none; }
  .contact__item {
    display: flex; align-items: center; gap: 7px;
    font-size: 15px; line-height: 24.5px;
  }
  .contact__icon { width: 12px; height: 12px; fill: var(--paper); flex: none; }
  .contact__address { font-size: 15px; margin-top: 6px; margin-left: -2px; }

  /* Back */
  .card--back { left: 388px; top: 505px; width: 567px; height: 352px; }
  .back__band {
    position: absolute; left: 0; top: 110px; width: 100%; height: 131px;
    background: linear-gradient(180deg, var(--sky) 0%, var(--mid-blue) 60%, var(--royal) 100%);
    display: flex; align-items: center; justify-content: center;
  }
  .back__name {
    color: var(--paper); font-size: 28px; font-weight: 600; letter-spacing: -0.2px;
  }
</style>
</head>
<body>
<main class="stage">
  <section class="card card--front" aria-label="Business card front">
    <div class="brand">
      <span class="brand__mark"></span>
      <span class="brand__name">Bramblefield Growth Partners</span>
    </div>
    <div class="front__band">
      <p class="person__name">Malcolm Dervaney</p>
      <p class="person__role">Owner</p>
      <ul class="contact">
        <li class="contact__item">
          <svg class="contact__icon" viewBox="0 0 24 24" aria-hidden="true"><path d="M6.6 10.8a15 15 0 0 0 6.6 6.6l2.2-2.2c.3-.3.7-.4 1-.2 1.1.4 2.3.6 3.6.6.6 0 1 .4 1 1V20c0 .6-.4 1-1 1A17 17 0 0 1 3 4c0-.6.4-1 1-1h3.5c.6 0 1 .4 1 1 0 1.3.2 2.5.6 3.6.1.3 0 .7-.2 1z"/></svg>
          0418923047
        </li>
        <li class="contact__item">
          <svg class="contact__icon" viewBox="0 0 24 24" aria-hidden="true"><path d="M2 5h20v14H2z M2 5l10 8 10-8" stroke="#ffffff" stroke-width="0"/><path d="M3 6l9 7 9-7" fill="none" stroke="#2a7fc0" stroke-width="2"/></svg>
          malcolm@bgp.com.au
        </li>
        <li class="contact__item">
          <svg class="contact__icon" viewBox="0 0 24 24" aria-hidden="true"><circle cx="12" cy="12" r="11"/><path d="M1 12h22M12 1c-4 4-4 18 0 22M12 1c4 4 4 18 0 22" fill="none" stroke="#2a7fc0" stroke-width="1.8"/></svg>
          bramblefieldgrowth.com.au
        </li>
      </ul>
      <p class="contact__address">58 Quorrin Ct, Elmbridge Vic 3190</p>
    </div>
  </section>

  <section class="card card--back" aria-label="Business card back">
    <div class="back__band">
      <span class="back__name">Bramblefield Growth Partners</span>
    </div>
  </section>
</main>
</body>
</html>
```